FREE BBQ for life if you win our business with your creative menu design

Looking for a 11x17 size menu. we are a full service BBQ restaurant. We have an upscale environment as well as up scale service. We offer 5 star dinning at a casual price. we are on route 84 and are proud of that. we offer the finest smoked meats. Specializing in smoked pork beef and bison. we have an old barn wood decor. we only use oak to smoke our meats. use a lot of tarnished metal as well as some string nail art. Looking for a menu that goes along our style. i have attached as many pictures as i could to give you a fill of how we do it out here.
PLEASE USE THE 11"X17" MENU TEMPLATE ATTACHED IN THE PROJECT BRIEF.
Target Market(s)
Cool people and there families.
Industry/Entity Type
Business
Requirements
Must have
- I have attached the Current menu we use. File brantlys menu pub. Those are all the Items. There will be some changes as we but together the new menu. The prices are changing. but that should be an easy change as we go.
Nice to have
- We are getting away from the lunch dinner menu and going to an all day menu. so rather than coming with toast or bun we will now be asking as an option. I have attached a menu i tried to make as a sample of how we will be doing it. new menu single page and new menu single page flame. These are ideas i had but could not really make it work. so use them as an idea of what we are looking for but be creative.

```html
<!DOCTYPE html>
<html lang="en">
<head>
<meta charset="utf-8">
<title>Brantlys Barbeque Menu</title>
<link rel="stylesheet" href="https://fonts.googleapis.com/css2?family=Alfa+Slab+One&family=Arimo:wght@400;700&display=swap">
<style>
:root{
  --bg:#d9d9d9;
  --ink:#1b1208;
  --desc:#3a2c1e;
  --red:#e0211b;
  --paper-light:#f6e9c8;
  --paper-dark:#e2c992;
  --ember:#d2551a;
  --char:#120806;
  --wood-light:#6b4a35;
  --wood-dark:#3b271b;
  --plaque-text:#fbf6ec;
  --gf-blue:#2c3d96;
  --app-blue:#2aa7e0;
}
*{margin:0;padding:0;box-sizing:border-box}
html,body{width:857px;height:1200px;overflow:hidden;background:var(--bg)}
.canvas{position:relative;width:857px;height:1200px}
.menu{position:absolute;left:36px;top:0;width:820px;height:1255px;transform:scale(.956);transform-origin:0 0;font-family:"Arimo",Arial,sans-serif;color:var(--ink);overflow:hidden}
.fire-backdrop{position:absolute;inset:0;background:
  radial-gradient(ellipse at 85% 10%,#f07a22 0,#b8380f 18%,transparent 40%),
  radial-gradient(ellipse at 95% 70%,#a3330c 0,transparent 35%),
  radial-gradient(ellipse at 50% 100%,#c4481a 0,transparent 30%),
  var(--char)}
.paper{position:absolute;left:30px;top:150px;width:757px;height:1035px;
  background:radial-gradient(ellipse at 50% 45%,var(--paper-light) 0,var(--paper-light) 45%,var(--paper-dark) 100%);
  clip-path:polygon(0 9%,50% 9%,52% 4%,100% 4%,99.5% 20%,100% 40%,99.4% 60%,100% 80%,99.6% 100%,0 99.6%,0.6% 70%,0 40%)}
.paper-top{position:absolute;left:30px;top:100px;width:757px;height:100px;background:var(--paper-light);clip-path:polygon(55% 100%,55% 55%,100% 45%,100% 100%)}
.brand-box{position:absolute;left:50px;top:0;width:360px;height:145px;border-radius:0 0 16px 16px;
  background:linear-gradient(180deg,#f7b64a 0%,#e2611c 60%,#9a2c0c 100%);display:flex;flex-direction:column;align-items:center;justify-content:center}
.brand-name{font-family:"Alfa Slab One",Georgia,serif;font-size:30px;color:#1f2a6b;letter-spacing:1px}
.brand-phone{font-weight:700;font-size:12px;color:var(--char);margin-top:4px}
.plaque{position:absolute;height:45px;background:linear-gradient(180deg,var(--wood-light),var(--wood-dark));box-shadow:2px 3px 4px rgba(0,0,0,.35);
  font-family:"Alfa Slab One",Georgia,serif;color:var(--plaque-text);font-size:30px;letter-spacing:1.5px;line-height:45px;text-align:center}
.item{position:absolute;width:297px}
.item h3{font-size:14px;font-weight:700;line-height:16px}
.item h3 .price,.price{color:var(--red);font-weight:400}
.item h3 small{font-size:10px;font-weight:700}
.item p{font-size:9.5px;line-height:12px;color:var(--desc);text-align:justify}
.note{position:absolute;font-size:11.5px;font-weight:700;line-height:14px;width:297px;text-align:justify}
.note::before{content:"*";position:absolute;left:-14px;font-size:15px}
.note.red{color:var(--red)}
.note.red::before{content:"* *";left:-27px}
.badge{position:absolute;display:flex;align-items:center;gap:4px;font-size:11px;font-weight:700}
.sides{position:absolute;font-size:13.5px;font-weight:700;line-height:17px}
.drink-mark{position:absolute;left:692px;width:49px;height:19px;border-radius:2px}
.tea-row{position:absolute;top:1126px;font-size:14px;font-weight:700;text-align:center}
.tea-row .price{display:block;font-weight:400;margin-top:1px}
.footer{position:absolute;left:428px;top:1205px;display:flex;align-items:center;gap:12px;color:#fff;font-size:11px;font-weight:700;line-height:14px}
.footer .app{font-size:20px;color:var(--app-blue);font-weight:400}
</style>
</head>
<body>
<div class="canvas">
<div class="menu">
  <div class="fire-backdrop" role="img" aria-label="Flames glowing around the menu sheet"></div>
  <div class="paper-top"></div>
  <div class="paper"></div>

  <header class="brand-box" role="img" aria-label="Brantlys Barbeque name plate over grilled food">
    <span class="brand-name">BRANTLYS BARBEQUE</span>
    <span class="brand-phone">505-555-0148</span>
  </header>

  <!-- Bison -->
  <div class="plaque" style="left:70px;top:188px;width:150px">BISON</div>
  <div class="badge" style="left:265px;top:195px;color:var(--red)"><svg width="32" height="32"><circle cx="16" cy="16" r="15" fill="#f3c9b8" stroke="#e0211b" stroke-width="1.5"/></svg>Heart Healthy</div>
  <div class="item" style="left:91px;top:246px"><h3>Bison Brisket - <span class="price">18.65</span></h3><p>The belly of beast, smoked then sliced thin and grilled. Juicy and tender</p></div>
  <div class="item" style="left:91px;top:302px"><h3>Bison Burger - <span class="price">12.59</span></h3><p>Smoked then grilled served with pepper jack cheese lettuce tomato pickle toped with spicy ranch.</p></div>
  <div class="item" style="left:91px;top:357px"><h3>Bison Steak - <span class="price">34.56</span></h3><p>12oz of lean healthy meat cooked to your desired temp.</p></div>
  <div class="note" style="left:91px;top:399px">Served with 1 sides and your choice of Texas toast, Kaiser bun, or Glutton Free bread</div>

  <!-- Smoked -->
  <div class="plaque" style="left:76px;top:455px;width:195px">SMOKED</div>
  <div class="badge" style="left:285px;top:467px;color:var(--gf-blue)"><svg width="28" height="28"><circle cx="14" cy="14" r="13" fill="none" stroke="#2c3d96" stroke-width="2.5"/></svg>Glutton free</div>
  <div class="item" style="left:97px;top:513px"><h3>Baby Back Ribs - <small>Full Rack</small> <small class="price">22.59</small> <small>- Half Rack</small> <small class="price">12.49</small></h3><p>Tender to the bone, finger licking good, never need a knife, best ribs you'll ever have.</p></div>
  <div class="item" style="left:97px;top:566px"><h3>St. Louis Ribs - <small>Half</small> <small class="price">16.45</small> <small>- Full</small> <small class="price">30.89</small></h3><p>A nice big tender rib , slow smoked, so tender that you can sink your teeth into.</p></div>
  <div class="item" style="left:97px;top:620px"><h3>Beef Brisket - <span class="price">10.95</span></h3><p>The most insane mouth watering smoky, moist, succulent piece of meat your mouth will ever have.</p></div>
  <div class="item" style="left:97px;top:673px"><h3>Pulled Pork - <span class="price">9.59</span></h3><p>Smoked for 18-20 hrs. then pulled and mixed with our signature base barbeque sauce .</p></div>
  <div class="item" style="left:97px;top:727px"><h3>Sliced Pork - <span class="price">10.54</span></h3><p>Smoked juicy tenderloin sliced thin then grilled per order .</p></div>
  <div class="item" style="left:97px;top:768px"><h3>Smoked Turkey - <span class="price">11.49</span></h3><p>Breast meat smoked and sliced. Juicy and tender .</p></div>
  <div class="item" style="left:97px;top:809px"><h3>Smoked Chicken half - <span class="price">13.59</span></h3><p>Moist and juicy smoked Breast and thigh on the bone basted with our signature sauce on the grill.</p></div>
  <div class="item" style="left:97px;top:862px"><h3>Rib Eye - <span class="price">21.95</span></h3><p>12oz juicy steak grilled to your desired temp</p></div>
  <div class="note" style="left:97px;top:907px">Served with 1 sides and your choice of Texas toast, Kaiser bun, or Glutton Free bread</div>
  <div class="note red" style="left:97px;top:942px">All meats are Glutton free Please specify if you are glutton Intolerant.</div>

  <!-- Sides -->
  <div class="plaque" style="left:70px;top:998px;width:142px">SIDES</div>
  <div class="sides" style="left:91px;top:1057px">*Green Chile Creamed Corn<br>*Potato Salad<br>*Baked Potato<br>*Grilled Veggies</div>
  <div class="sides" style="left:294px;top:1074px">*Baked Beans<br>*Waffle Fries<br>*Coleslaw</div>
  <div class="sides" style="left:91px;top:1143px;color:var(--red);font-weight:400">**Extra side 2.29</div>

  <!-- Appetizers -->
  <div class="plaque" style="left:428px;top:130px;width:282px">APPETIZERS</div>
  <div class="item" style="left:449px;top:189px;width:292px"><h3>King Rings - <span class="price">7.89</span></h3><p>Green Chili battered fried golden crispy 1" thick onion rings. Served with spicy ranch.</p></div>
  <div class="item" style="left:449px;top:242px;width:292px"><h3>Deep Fried Pickles - <span class="price">7.89</span></h3><p>Crisp dill pickle chips battered and fried to a golden crispy brown. Served with spicy ranch.</p></div>
  <div class="item" style="left:449px;top:296px;width:292px"><h3>Fried Okra - <span class="price">7.89</span></h3><p>Okra is breaded then fried until golden. Served with spicy ranch.</p></div>
  <div class="item" style="left:449px;top:337px;width:292px"><h3>Green Chili Waffle Fries - <span class="price">7.89</span></h3><p>Crispy waffle-cut Fries, topped with a savory blend of cheese, and New Mexico green chile. Served with spicy ranch.</p></div>
  <div class="item" style="left:449px;top:390px;width:292px"><h3>KC Wild Wings - <span class="price">9.99</span></h3><p>Big, meaty pork wings, deep fried to a perfect golden brown, tossed in a hot Buffalo-style sauce, and served with spicy buttermilk ranch dressing on the side. Served with spicy ranch.</p></div>
  <div class="item" style="left:449px;top:461px;width:292px"><h3>Sampler Platter - <span class="price">8.99</span></h3><p>Two KC Wild Wings, 6oz of Fried Pickles, 6oz of King Rings. Served with spicy ranch.</p></div>

  <!-- Salads -->
  <div class="plaque" style="left:428px;top:536px;width:200px">SALADS</div>
  <div class="item" style="left:449px;top:595px;width:292px"><h3>All you can eat salad bar - <span class="price">7.89</span></h3><p>Enjoy as much salad as you would like</p></div>
  <div class="item" style="left:449px;top:641px;width:292px"><h3>Meaty Salad - <span class="price">3.00</span></h3><p>Choose any meat to add to your salad 3oz of meat .<br>(Excludes ribs and bison.)</p></div>
  <div class="item" style="left:449px;top:695px;width:292px"><h3>Side Salad - <small>With out meal</small> <small class="price">3.00</small> <small>- Add to meal</small> <small class="price">1.50</small></h3></div>

  <!-- Desserts -->
  <div class="plaque" style="left:428px;top:743px;width:224px">DESSERTS</div>
  <div class="item" style="left:449px;top:804px;width:292px"><h3>Peach Cobbler <span class="price">&amp;</span> Ice Cream - <small>large</small> <small class="price">5.89</small> <small>Small</small> <small class="price">3.29</small></h3><p>Served hot topped with ice cream.</p></div>
  <div class="item" style="left:449px;top:850px;width:292px"><h3>Cookies A-L-Mode - <small>large</small> <small class="price">5.89</small> <small>Small</small> <small class="price">3.29</small></h3><p>Hot gooey cookies topped with ice cream your choice chocolate chip or macadamia nut. large 5.89 Small</p></div>
  <div class="note" style="left:449px;top:907px;font-size:11px">Dessert of the week<br><span style="color:var(--red)">Ask your server for our special dessert of the week</span></div>

  <!-- Drinks -->
  <div class="plaque" style="left:428px;top:970px;width:179px">DRINKS</div>
  <div class="drink-mark" style="top:1026px;background:#1d4fa8"></div>
  <div class="drink-mark" style="top:1051px;background:#8e1b22"></div>
  <div class="item" style="left:449px;top:1027px;width:240px"><h3>Lemonade - <span class="price">2.59</span></h3><p>Regular, Strawberry, Watermelon, Cherry, Peach</p></div>
  <div class="item" style="left:449px;top:1068px;width:292px"><h3>Fountain - <span class="price">1.89</span></h3><p>Summit Cola, Doc Ridge , Root Beer , Mesa Lime, Canyon Dew , Summit Diet, Doc Ridge Diet</p></div>
  <div class="tea-row" style="left:449px">Iced Teas<span class="price">1.89</span></div>
  <div class="tea-row" style="left:553px">Coffee<span class="price">2.69</span></div>
  <div class="tea-row" style="left:645px">Hot Chocolate<span class="price">2.89</span></div>

  <footer class="footer"><span class="app">Tally</span><span>Join our Customer loyalty app.<br>Get free food when you become a loyal customer.</span></footer>
</div>
</div>
</body>
</html>
```